Banner ads for LP that work with same theme as below banners

Love the banner ads below. Need more with attached photos. But use the same wording, font as in below banner ads. Should be LP size 1200/627 so I can use for Pixorly and LP. Looking for great ads to use as LP ads. We do lots of ads so it will be worth your time to enter this contest you will be rewarded with a ton of work. Need several banner ads that work together. So maybe 1 of the dresses, 1 of the sweater, 1 of the leggings, 1 of the jacket

Target Market(s)

Women 24-45

Industry/Entity Type

Fashion

Requirements
Must have
• Banner ads that work for LP and Pixorly
Nice to have
• Several options to choose from
Should not have
• not sure

```html
<!DOCTYPE html>
<html lang="en">
<head>
<meta charset="utf-8">
<title>Our Best Leggings Ever – Banner</title>
<link rel="stylesheet" href="https://fonts.googleapis.com/css2?family=Yesteryear&family=Bodoni+Moda:wght@500&family=Tinos:wght@400;700&display=swap">
<style>
  :root {
    --gold: #e29a22;
    --gold-light: #efb236;
    --gold-deep: #c9801a;
    --amber-brown: #9a5a1c;
    --black: #0b0b0b;
    --lime: #d3d92a;
    --ink: #111111;
    --button-brown: #9b5c2a;
    --button-frame: #f0c98a;
    --white: #ffffff;
    --legging-black: #141217;
    --legging-pink: #d51e8c;
  }
  * { margin: 0; padding: 0; box-sizing: border-box; }
  html, body { width: 1200px; height: 627px; overflow: hidden; background: var(--gold); }
  .banner { position: relative; width: 1200px; height: 627px; overflow: hidden; background: var(--gold); }
  .backdrop { position: absolute; inset: 0; }
  .headline { position: absolute; left: 60px; top: 175px; width: 440px; text-align: center; color: var(--ink); }
  .headline-script { font-family: "Yesteryear", cursive; font-size: 72px; line-height: 1; display: block; }
  .headline-script.ever { margin-top: 8px; font-size: 80px; padding-right: 70px; }
  .headline-caps { font-family: "Bodoni Moda", serif; font-weight: 500; font-size: 58px; letter-spacing: 0.32em; line-height: 1.15; display: block; margin-top: 22px; padding-left: 18px; }
  .cta { position: absolute; left: 42px; top: 468px; width: 406px; height: 90px; padding: 10px 13px; background: var(--button-frame); opacity: 0.95; }
  .cta-inner { width: 100%; height: 100%; background: var(--button-brown); display: flex; align-items: center; justify-content: center; font-family: "Tinos", serif; font-size: 38px; color: var(--white); letter-spacing: 0.01em; text-decoration: none; }
  .cta-inner b { font-weight: 700; }
  .cta-inner span { margin: 0 10px; font-weight: 400; }
  .product-photo { position: absolute; left: 535px; top: 0; width: 515px; height: 627px;
    background: linear-gradient(90deg, var(--legging-black) 0 33%, var(--legging-pink) 33% 66%, var(--legging-black) 66% 100%); }
</style>
</head>
<body>
<main class="banner">
  <svg class="backdrop" width="1200" height="627" viewBox="0 0 1200 627" aria-hidden="true">
    <rect width="1200" height="627" fill="var(--gold)"/>
    <polygon points="0,150 0,627 560,627" fill="var(--gold-deep)" opacity="0.35"/>
    <polygon points="300,627 1200,627 1200,300" fill="var(--gold-light)" opacity="0.35"/>
    <polygon points="0,35 620,0 0,150" fill="var(--amber-brown)" opacity="0.8"/>
    <polygon points="0,0 1200,0 1200,60 0,35" fill="var(--black)"/>
    <polygon points="1000,60 1200,40 1200,200" fill="var(--lime)"/>
    <polygon points="1040,200 1200,200 1200,627 1080,627" fill="var(--gold-light)" opacity="0.5"/>
  </svg>

  <h1 class="headline">
    <span class="headline-script">Our Best</span>
    <span class="headline-caps">LEGGINGS</span>
    <span class="headline-script ever">Ever!</span>
  </h1>

  <div class="cta">
    <a class="cta-inner" href="#"><b>SHOP</b><span>THE</span><b>LOOK</b></a>
  </div>

  <div class="product-photo" role="img" aria-label="Photo of three models' legs wearing leggings: black with white lace bands, solid pink, and black with white lace bands"></div>
</main>
</body>
</html>
```